Inspirational Quotes Poster Set

Brookloft is a stylish coworking space, which has a design-oriented vintage look from the 60's with an industrial touch (www.brookloft-example.com) Brookloft Quote Poster Set of 16 posters. The poster should be typo oriented and rather simple. Reflecting a bit the clean billboard design from the sixties. Minimal / simple graphical elements

Target Market(s)

Startups and Entrepreneurs

Industry/Entity Type

Startup

Font styles to use
Sans Serif

Colors

Designer to choose colors to be used in the design.

Requirements
Must have
• Posters need to be on and very stylish

```html
<!DOCTYPE html>
<html lang="en">
<head>
<meta charset="utf-8">
<title>Brookloft Quote Poster Set – Always Challenge the Old Ways</title>
<link rel="stylesheet" href="https://fonts.googleapis.com/css2?family=Familjen+Grotesk:wght@600;700&display=swap">
<style>
  :root {
    --poster-gold: #c9a20c;
    --ink-white: #ffffff;
  }
  html, body {
    margin: 0;
    padding: 0;
    width: 801px;
    height: 1200px;
    overflow: hidden;
    background: var(--poster-gold);
  }
  .poster {
    display: block;
    width: 801px;
    height: 1200px;
    background: var(--poster-gold);
  }
  .quote-word {
    font-family: "Familjen Grotesk", "Helvetica Neue", Arial, sans-serif;
    font-weight: 700;
    font-size: 345px;
    fill: var(--ink-white);
  }
  .rule {
    stroke: var(--ink-white);
    stroke-width: 2.5;
  }
  .credit {
    font-family: "Familjen Grotesk", "Helvetica Neue", Arial, sans-serif;
    font-weight: 700;
    font-size: 46px;
    letter-spacing: 1px;
    fill: var(--ink-white);
  }
  .brand-name {
    font-family: "Familjen Grotesk", "Helvetica Neue", Arial, sans-serif;
    font-weight: 700;
    font-size: 76px;
    fill: var(--ink-white);
  }
</style>
</head>
<body>
<svg class="poster" viewBox="0 0 1568 2350" preserveAspectRatio="none" xmlns="http://www.w3.org/2000/svg" aria-labelledby="quote-title">
  <title id="quote-title">Always challenge the old ways — Harold Whitman, CEO Copperleaf Coffee</title>
  <defs>
    <clipPath id="upper-band">
      <polygon points="0,568 1568,254 1568,988.6 0,1302"/>
    </clipPath>
    <clipPath id="lower-band">
      <polygon points="0,1302 1568,988.6 1568,1557 0,1869"/>
    </clipPath>
  </defs>

  <rect width="1568" height="2350" fill="var(--poster-gold)"/>

  <g class="quote-upper" clip-path="url(#upper-band)">
    <text class="quote-word" x="51" y="712" textLength="1147" lengthAdjust="spacingAndGlyphs">always</text>
    <text class="quote-word" x="-6" y="1025" textLength="1660" lengthAdjust="spacingAndGlyphs">challenge</text>
  </g>

  <g class="quote-lower" clip-path="url(#lower-band)">
    <text class="quote-word" x="431" y="1406" textLength="1190" lengthAdjust="spacingAndGlyphs">the old</text>
    <text class="quote-word" x="430" y="1644" textLength="848" lengthAdjust="spacingAndGlyphs">ways</text>
  </g>

  <line class="rule" x1="30" y1="562" x2="1083" y2="350"/>
  <line class="rule" x1="376" y1="1227" x2="1568" y2="988"/>
  <line class="rule" x1="223" y1="1825" x2="1368" y2="1597"/>

  <text class="credit" x="139" y="2033">Harold Whitman,</text>
  <text class="credit" x="139" y="2088">CEO Copperleaf Coffee</text>

  <text class="brand-name" x="784" y="2237" text-anchor="middle">Brookloft</text>
</svg>
</body>
</html>
```